Business Card for Fashion House

We need a business card design for our personalize fashion service for our customers. the business card should reflect reliability, luxury and creativity.
The brand Gravetto is extracted from "Graceful Velvetto"; Gravetto provides fashion designs sprinkled with luxury and style tailored for our elite clients character profile.
Gravetto is created for those who embody class and elegance with a passion for style.
Target Market(s)
Affluent Customers
Industry/Entity Type
Fashion
Contact Information for Business Card
Samira Haddadin
Fashion Designer
Telephone: +971 4 555 0192
Mobile +971 50 555 0147
Emal info@gravetto-example.com
Website www.gravetto-example.com
Social Media Youtube g+ Facebook Instagram Pin /gravetto
Font styles to use
Other font styles liked:
- Audrey provided
Look and feel
Each slider illustrates characteristics of the customer's brand and the style your logo design should communicate.

```html
<!DOCTYPE html>
<html lang="en">
<head>
<meta charset="utf-8">
<title>Gravetto — Business Card</title>
<link href="https://fonts.googleapis.com/css2?family=Tenor+Sans&display=swap" rel="stylesheet">
<style>
  :root {
    --stage: #141414;
    --card: #080808;
    --card-edge: #1e1e1e;
    --ink: #f2f2f2;
    --ink-soft: #d6d6d6;
  }
  * { margin: 0; padding: 0; box-sizing: border-box; }
  html, body {
    width: 1200px;
    height: 864px;
    overflow: hidden;
    background: var(--stage);
    font-family: "Tenor Sans", "Optima", sans-serif;
    color: var(--ink);
  }
  .stage {
    width: 1200px;
    height: 864px;
    display: flex;
    align-items: center;
    justify-content: center;
    gap: 44px;
  }
  .card {
    width: 520px;
    height: 297px;
    background: var(--card);
    border: 1px solid var(--card-edge);
    position: relative;
  }
  /* Front side */
  .card--front {
    display: flex;
    flex-direction: column;
    align-items: center;
    justify-content: center;
    gap: 22px;
  }
  .brand-dot {
    width: 44px;
    height: 44px;
    border: 2px solid var(--ink);
    border-radius: 50%;
  }
  .brand-name {
    font-size: 26px;
    letter-spacing: 0.42em;
    margin-right: -0.42em;
    text-transform: uppercase;
  }
  /* Back side */
  .card--back {
    display: flex;
    align-items: center;
    padding: 0 40px 0 48px;
  }
  .back-brand {
    width: 150px;
    display: flex;
    flex-direction: column;
    align-items: center;
    gap: 14px;
  }
  .back-brand .brand-dot { width: 56px; height: 56px; }
  .back-brand .brand-name { font-size: 15px; letter-spacing: 0.3em; margin-right: -0.3em; }
  .divider {
    width: 1.5px;
    height: 150px;
    background: var(--ink);
    margin: 0 22px 0 18px;
  }
  .details { display: flex; flex-direction: column; }
  .person-name { font-size: 17px; letter-spacing: 0.04em; }
  .person-role { font-size: 12px; color: var(--ink-soft); margin-top: 2px; margin-bottom: 16px; }
  .contact-list { list-style: none; display: flex; flex-direction: column; gap: 7px; }
  .contact-item {
    display: flex;
    align-items: center;
    gap: 10px;
    font-size: 12.5px;
    letter-spacing: 0.04em;
  }
  .contact-icon { width: 13px; height: 13px; flex: none; }
</style>
</head>
<body>
<main class="stage">
  <section class="card card--front" aria-label="Card front">
    <div class="brand-dot"></div>
    <div class="brand-name">Gravetto</div>
  </section>

  <section class="card card--back" aria-label="Card back">
    <div class="back-brand">
      <div class="brand-dot"></div>
      <div class="brand-name">Gravetto</div>
    </div>
    <div class="divider"></div>
    <div class="details">
      <div class="person-name">Samira Haddadin</div>
      <div class="person-role">Fashion Designer</div>
      <ul class="contact-list">
        <li class="contact-item">
          <svg class="contact-icon" viewBox="0 0 16 16" fill="none" stroke="currentColor" stroke-width="1.2"><circle cx="8" cy="8" r="7.2"/><path d="M5 5.5c0-.6.4-1 1-1h.5l.8 2-.8.6c.4 1 1.2 1.8 2.2 2.2l.6-.8 2 .8v.5c0 .6-.4 1-1 1C7.5 10.8 5 8.3 5 5.5z"/></svg>
          +971 4 555 0192
        </li>
        <li class="contact-item">
          <svg class="contact-icon" viewBox="0 0 16 16" fill="none" stroke="currentColor" stroke-width="1.2"><circle cx="8" cy="8" r="7.2"/><rect x="5.6" y="3.8" width="4.8" height="8.4" rx="0.8"/><path d="M7.4 10.8h1.2"/></svg>
          +971 50 555 0147
        </li>
        <li class="contact-item">
          <svg class="contact-icon" viewBox="0 0 16 16" fill="none" stroke="currentColor" stroke-width="1.2"><circle cx="8" cy="8" r="7.2"/><rect x="4" y="5.2" width="8" height="5.6"/><path d="M4 5.4l4 3 4-3"/></svg>
          info@gravetto-example.com
        </li>
        <li class="contact-item">
          <svg class="contact-icon" viewBox="0 0 16 16" fill="none" stroke="currentColor" stroke-width="1.2"><circle cx="8" cy="8" r="7.2"/><ellipse cx="8" cy="8" rx="3" ry="7.2"/><path d="M1 8h14M2.2 4.5h11.6M2.2 11.5h11.6"/></svg>
          www.gravetto-example.com
        </li>
      </ul>
    </div>
  </section>
</main>
</body>
</html>
```